Wedding filmmaker needs artistic business card design - brightwaterreels.ca

We are high end wedding filmmakers in a major market who produce cinematic wedding films. We require a business card design that communicates our quality, artistry, and professionalism yet looks progressive and friendly. Colors and design should skew appeal more to the bride-to-be who is usually the decision maker but not be overtly feminine per se. This means generally light pastel shades of ivory, purple, pink, yellow, as examples.
We already have a name logo established: the words "Brightwater Reels" in the font Great Vibes. Designs must use Kraft natural cardstock as the print stock and am leaning heavily toward our name logo in white, but I am open to black as well. Please design any color elements with spot white underneath where possible.
Do not try to compliment or take inspiration from our website design. Treat the card design as a separate stand alone.
Thank you so much for your hard work!

Target Market(s)

Affluent couples spending $50,000+ on their wedding

Industry/Entity Type

Progressive

Contact Information for Business Card

Peter Brightwater
Producer
905-482-7139
www.brightwaterreels.ca
peter@brightwaterreels.ca
twitter @brightwater287

Font styles to use
Serif
Sans Serif

Requirements
Must have
• - Brightwater Reels name logo (reference GIF uploaded for reference only) and catch phrase: Breathtaking wedding films (I'm open to capitalizing all three words, or just first, or all in small caps). I favor logo, and catch phrase on front of card and my contact details on the other side but if you feel strongly about a different design, go for it!
• - Design must be submitted shown on Kraft natural cardstock NOT WHITE cardstock, If you're not familiar with Kraft, this is what it looks like: http://www.quillandlatchjournal.com/wp-content/uploads/2013/07/il_570xN.382745196_kq3m.jpg
Nice to have
• - An original graphic element (eg. movie reel, bouquet, confetti, etc.) that compliments the name logo but is subtle and discreet, doesn't overpower or entangle it.
• -Great use of balance, composition, negative space, etc. I like clean tasteful design
Should not have
• -Lousy boring clip art.
• -Graphic elements, fonts, or color palette from our website
• -White cardstock background
• -designs you have previously submitted for other contests
• -Bold dark colors (eg. red, orange navy blue, etc.)
• -High tech futuristic designs like you'd create for a software company

```html
<!DOCTYPE html>
<html lang="en">
<head>
<meta charset="utf-8">
<title>Brightwater Reels – Business Card</title>
<link href="https://fonts.googleapis.com/css2?family=Cormorant+Garamond:wght@500;600&family=Great+Vibes&family=Montserrat:wght@400;500;600&display=swap" rel="stylesheet">
<style>
  :root {
    --backdrop: #ecebe8;
    --kraft-light: #cfa97f;
    --kraft: #bf9468;
    --lavender: #d9cbe6;
    --lavender-deep: #c4b0d8;
    --blush: #f3d9dc;
    --ivory: #fffdf6;
    --ink: #4a382a;
    --ink-soft: #5e4a39;
  }
  * { margin: 0; padding: 0; box-sizing: border-box; }
  html, body {
    width: 1200px; height: 899px; overflow: hidden;
    background: var(--backdrop);
  }
  .canvas {
    position: relative; width: 1200px; height: 899px;
    display: flex; align-items: center; justify-content: center;
  }
  .business-card {
    position: relative; width: 1000px; height: 571px;
    border-radius: 56px; overflow: hidden;
    background: radial-gradient(ellipse at 62% 38%, var(--kraft-light) 0%, var(--kraft) 85%);
    box-shadow: 0 6px 22px rgba(0,0,0,0.14);
  }
  .corner-swoops { position: absolute; inset: 0; width: 100%; height: 100%; }
  .brand-name {
    position: absolute; left: 230px; top: 104px; width: 720px;
    text-align: center;
    font-family: "Great Vibes", cursive;
    font-size: 96px; font-weight: 400; line-height: 1.2; color: var(--ivory);
    white-space: nowrap;
  }
  .tagline {
    position: absolute; left: 230px; top: 232px; width: 720px;
    text-align: center;
    font-family: "Cormorant Garamond", serif;
    font-size: 24px; font-weight: 600; font-variant: small-caps;
    letter-spacing: 4px; color: var(--ink);
  }
  .contact-list {
    position: absolute; left: 58px; top: 330px;
    list-style: none;
    font-family: "Montserrat", sans-serif;
    font-size: 17px; color: var(--ink); letter-spacing: 0.5px;
  }
  .contact-list li {
    display: flex; align-items: center; gap: 14px; height: 30px;
  }
  .contact-icon { width: 17px; height: 17px; flex: none; fill: var(--ink-soft); }
  .person {
    position: absolute; left: 560px; top: 320px; width: 320px;
    text-align: center;
    font-family: "Montserrat", sans-serif;
  }
  .person-name {
    font-size: 24px; font-weight: 600; letter-spacing: 2px; color: var(--ink);
  }
  .person-title {
    margin-top: 4px;
    font-size: 17px; color: var(--ink-soft); letter-spacing: 0.5px;
  }
  .address {
    position: absolute; left: 560px; top: 418px; width: 320px;
    text-align: center;
    font-family: "Montserrat", sans-serif; font-style: normal;
    font-size: 18px; line-height: 28px; color: var(--ink); letter-spacing: 0.5px;
  }
</style>
</head>
<body>
<main class="canvas">
  <section class="business-card">
    <svg class="corner-swoops" viewBox="0 0 1000 571" aria-hidden="true">
      <path d="M0 0 H235 C150 25 55 110 0 250 Z" fill="var(--lavender)"/>
      <path d="M235 0 C150 25 55 110 0 250 L0 282 C45 140 135 40 262 0 Z" fill="var(--blush)"/>
      <path d="M1000 571 H812 C900 545 968 450 1000 330 Z" fill="var(--lavender-deep)"/>
      <path d="M812 571 C900 545 968 450 1000 330 L1000 298 C972 430 900 535 778 571 Z" fill="var(--blush)"/>
    </svg>

    <h1 class="brand-name">Brightwater Reels</h1>
    <p class="tagline">Breathtaking Wedding Films</p>

    <ul class="contact-list">
      <li>
        <svg class="contact-icon" viewBox="0 0 24 24"><path d="M6 2 L10 2 L11 7 L8.5 9 C10 12.5 11.5 14 15 15.5 L17 13 L22 14 L22 18 C22 20 20 22 18 22 C9 21 3 15 2 6 C2 4 4 2 6 2 Z"/></svg>
        <span>905-482-7139</span>
      </li>
      <li>
        <svg class="contact-icon" viewBox="0 0 24 24"><circle cx="12" cy="12" r="10"/><text x="12" y="17" text-anchor="middle" font-size="14" font-family="Montserrat, sans-serif" font-weight="600" fill="var(--kraft-light)">@</text></svg>
        <span>@brightwater287</span>
      </li>
      <li>
        <svg class="contact-icon" viewBox="0 0 24 24"><rect x="2" y="5" width="20" height="14" rx="1.5"/><path d="M3 6 L12 13 L21 6" fill="none" stroke="var(--kraft-light)" stroke-width="2"/></svg>
        <span>peter@brightwaterreels.ca</span>
      </li>
      <li>
        <svg class="contact-icon" viewBox="0 0 24 24"><circle cx="12" cy="12" r="10"/><path d="M2 12 H22 M12 2 C7 7 7 17 12 22 M12 2 C17 7 17 17 12 22" fill="none" stroke="var(--kraft-light)" stroke-width="1.5"/></svg>
        <span>www.brightwaterreels.ca</span>
      </li>
    </ul>

    <div class="person">
      <p class="person-name">PETER BRIGHTWATER</p>
      <p class="person-title">Producer</p>
    </div>

    <address class="address">214.6th Floor.Quay<br>Harbour Lane ONT</address>
  </section>
</main>
</body>
</html>
```